Brivane Management

We need a web design for a new consulting company, with clients all over the world. The company provides management consulting to the travel industry.

Logo files are attached.

Website must look very corporate and be responsive in design.

Management Consulting

```html
<!DOCTYPE html>
<html lang="en">
<head>
<meta charset="utf-8">
<title>Brivane Management</title>
<link href="https://fonts.googleapis.com/css2?family=Oxygen:wght@300;400;700&family=Bree+Serif&display=swap" rel="stylesheet">
<style>
  :root{
    --blue:#0a6fbf;
    --navy:#14243f;
    --green:#7cb342;
    --icon:#1e1e1e;
    --text:#333;
    --muted:#555;
    --band:#ececec;
    --footer-top:#3b3b3b;
    --footer-bottom:#1d1d1d;
    --field:#fff;
    --submit:#0f4f8c;
  }
  *{box-sizing:border-box;margin:0;padding:0}
  html,body{width:882px;height:1200px;overflow:hidden;background:#fff}
  body{font-family:'Oxygen',sans-serif;color:var(--text);position:relative}
  .abs{position:absolute}
  .site-header{left:0;top:0;width:882px;height:77px;border-top:3px solid #9a9a9a;background:linear-gradient(#fff,#f1f1f1);border-bottom:1px solid #ddd}
  .brand{display:flex;align-items:center;gap:7px;font-family:'Oxygen',sans-serif;font-weight:700;color:var(--navy);white-space:nowrap}
  .brand-dot{width:40px;height:40px;border-radius:50%;background:var(--blue);flex:none}
  .site-header .brand{left:106px;top:20px;font-size:16.5px}
  .phone{right:105px;top:15px;font-size:15px;color:#222;display:flex;align-items:center;gap:6px}
  .main-nav{right:104px;top:46px;display:flex;font-size:11px}
  .main-nav a{color:#333;text-decoration:none;padding:0 11px;border-left:1px solid #bbb;line-height:14px}
  .main-nav a:first-child{border-left:0;color:var(--blue);text-decoration:underline}
  .hero{left:0;top:77px;width:882px;height:328px;background:
      radial-gradient(ellipse 260px 160px at 88% 8%,#c98f78 0,rgba(201,143,120,0) 100%),
      radial-gradient(ellipse 200px 120px at 66% 95%,#e0b9a3 0,rgba(224,185,163,0) 100%),
      radial-gradient(circle at 60% 55%,#f3f7fb 0,#b9cde0 18%,#7f9fbf 45%,#5f84a8 75%,#4a6f95 100%)}
  .hero-caption{left:0;top:372px;width:882px;height:33px;background:rgba(40,40,40,.6);color:#fff;font-size:19px;text-align:center;line-height:33px}
  .round-arrow{width:30px;height:30px;border-radius:50%;background:#1b1b1b;border:2px solid #555;display:flex;align-items:center;justify-content:center}
  .section-title{font-family:'Bree Serif',serif;font-size:19px;color:var(--navy);text-transform:uppercase;text-align:center;font-weight:400}
  .section-title b{color:var(--blue);font-weight:400}
  .about-title{left:0;top:418px;width:882px;display:flex;justify-content:center;align-items:center;gap:8px}
  .about-title .brand{font-size:12px}
  .about-title .brand-dot{width:28px;height:28px}
  .about-text{left:104px;top:455px;width:674px;font-size:10px;line-height:15.5px;text-align:center;color:var(--muted)}
  .services{left:0;top:535px;width:882px;height:198px;background:var(--band);border-top:1px solid #ddd;border-bottom:1px solid #ddd}
  .service{width:150px;text-align:center}
  .service-icon{width:76px;height:76px;border-radius:50%;margin:0 auto;background:radial-gradient(circle at 35% 45%,#f3f6f0 0,#dfe8d9 50%,#c4cbd2 100%);display:flex;align-items:center;justify-content:center}
  .service-name{font-family:'Bree Serif',serif;font-size:11.5px;line-height:11px;text-transform:uppercase;color:#222;margin-top:19px}
  .col-title{font-family:'Bree Serif',serif;font-size:16px;color:var(--navy);text-transform:uppercase;width:208px;border-bottom:2px solid #e3e3e3;padding-bottom:5px;display:flex;align-items:center;gap:6px;font-weight:400}
  .col-title b{color:var(--blue);font-weight:400}
  .news-item{font-size:9px;line-height:12.5px;color:#333;width:208px;letter-spacing:-.1px}
  .news-item strong{display:block;font-size:10px;color:#222}
  .read-more{font-size:9px;font-weight:700;color:var(--blue)}
  .quote{left:337px;top:797px;width:206px;height:96px;background:#ececec;border-radius:8px;padding:10px 8px 0 32px;font-size:9px;line-height:14px;font-style:italic;color:#444;letter-spacing:-.1px}
  .avatar{left:351px;top:877px;width:48px;height:48px;border:3px solid #fff;box-shadow:0 0 2px #999;background:linear-gradient(#c5cdd5,#8c99a6)}
  .field{background:var(--field);border:1px solid #bbb;border-radius:3px;font-size:9px;font-style:italic;color:#888;padding:4px 6px;width:207px}
  .submit{left:571px;top:913px;width:49px;height:17px;background:var(--submit);color:#fff;font-size:10px;font-weight:700;text-align:center;line-height:17px;border-radius:2px}
  .clients{left:0;top:955px;width:882px;height:130px;background:var(--band);border-top:1px solid #ddd}
  .client{height:55px;background:#fff;display:flex;align-items:center;justify-content:center;font-size:15px;font-weight:700;color:#333;gap:6px}
  .client i{width:12px;height:12px;display:block;background:#c21f2a}
  .site-footer{left:0;top:1085px;width:882px;height:115px;background:linear-gradient(var(--footer-top),var(--footer-bottom));color:#fff}
  .footer-box{top:19px;height:57px;background:#4a4a4a;border:1px solid #5e5e5e;padding:6px 9px;font-size:10.5px;font-weight:700}
  .footer-box p{font-weight:400;font-size:8.5px;color:#ddd;display:flex;align-items:center;gap:6px;margin-top:3px}
  .social-row{display:flex;gap:8px;margin-top:8px}
  .social{width:19px;height:19px;display:block;flex:none}
  .footer-links{left:105px;top:90px;font-size:8.5px;color:#ddd}
  .footer-links span{padding:0 4px}
  .copyright{right:104px;top:90px;font-size:8.5px;color:#ddd}
  .site-footer .brand{left:568px;top:26px;color:#fff;font-size:15px}
  .site-footer .brand-dot{background:#fff;width:40px;height:40px}
</style>
</head>
<body>
  <header class="site-header abs">
    <div class="brand abs"><span class="brand-dot"></span>BRIVANE MANAGEMENT</div>
    <div class="phone abs">
      <svg width="13" height="13" viewBox="0 0 13 13"><rect width="13" height="13" rx="2" fill="#0a6fbf"/><path d="M4 3l1.5 2-1 1c.5 1 1.5 2 2.5 2.5l1-1L10 9l-1 1.3C6 10 3.5 7 3 4z" fill="#fff"/></svg>
      555 010 2040
    </div>
    <nav class="main-nav abs"><a>Home</a><a>About Us</a><a>Services</a><a>Contact Us</a></nav>
  </header>

  <div class="hero abs" role="img" aria-label="Photo of a hand placing a blue jigsaw puzzle piece into a puzzle"></div>
  <div class="round-arrow abs" style="left:73px;top:216px"><svg width="8" height="10"><path d="M6 1L2 5l4 4" stroke="#fff" stroke-width="1.6" fill="none"/></svg></div>
  <div class="round-arrow abs" style="left:780px;top:216px"><svg width="8" height="10"><path d="M2 1l4 4-4 4" stroke="#fff" stroke-width="1.6" fill="none"/></svg></div>
  <div class="hero-caption abs">WE PROVIDE A CUSTOMIZED PLAN FOR FINANCIAL IMPROVEMENT</div>

  <div class="about-title abs">
    <span class="section-title"><b>About</b></span>
    <div class="brand"><span class="brand-dot"></span>BRIVANE MANAGEMENT</div>
  </div>
  <p class="about-text abs">Lorem ipsum dolor sit amet, consectetuer adipiscing elit,Sed diam nonummy nibh euismod tincidunt ut laoreet dolore magna aliquam erat volutpat. Ut wisi enim ad minim veniam, quis nostrud exerci tation ullamcorper suscipit lobortis nisl ut aliquip &nbsp;commodo consequat. Duis autem vel eum iriure dolor in hendrerit in vulputate velit esse molestie consequat, vel ill dolore eu feugiat nulla facilisis at vero eros et accumsan et iusto odio dignissim qui blandit praesent luptatumdeelenit augue duis dolore te feugait nulla facilisi.</p>

  <section class="services abs">
    <h2 class="section-title abs" style="left:0;top:18px;width:882px"><b>Our</b> Services</h2>
    <div class="service abs" style="left:94px;top:64px">
      <div class="service-icon"><svg width="46" height="42" viewBox="0 0 46 42"><rect x="6" y="26" width="6" height="14" fill="var(--icon)"/><rect x="15" y="21" width="6" height="19" fill="var(--icon)"/><rect x="24" y="16" width="6" height="24" fill="var(--icon)"/><rect x="33" y="11" width="6" height="29" fill="var(--icon)"/><path d="M4 22L20 12l7 4L40 5" stroke="var(--icon)" stroke-width="3" fill="none"/><path d="M34 2h9v9z" fill="var(--icon)"/></svg></div>
      <div class="service-name">Sales/<br>Marketing</div></div>
    <div class="service abs" style="left:223px;top:64px">
      <div class="service-icon"><svg width="40" height="40" viewBox="0 0 40 40"><circle cx="20" cy="20" r="16" fill="var(--icon)"/><circle cx="20" cy="20" r="12" fill="#fff"/><path d="M20 11v9l6 4" stroke="var(--icon)" stroke-width="2.5" fill="none"/></svg></div>
      <div class="service-name">Strategic<br>Planning</div></div>
    <div class="service abs" style="left:360px;top:64px">
      <div class="service-icon"><svg width="40" height="40" viewBox="0 0 40 40"><circle cx="20" cy="20" r="16" fill="var(--icon)"/><circle cx="20" cy="20" r="12.5" fill="none" stroke="#fff" stroke-width="1.5"/><text x="20" y="27" font-family="Oxygen,sans-serif" font-size="19" font-weight="700" fill="#fff" text-anchor="middle">$</text></svg></div>
      <div class="service-name" style="margin-top:17px">Human Capital<br>Management Solutions</div></div>
    <div class="service abs" style="left:511px;top:64px">
      <div class="service-icon"><svg width="42" height="40" viewBox="0 0 42 40"><rect x="3" y="5" width="28" height="22" fill="none" stroke="var(--icon)" stroke-width="3"/><path d="M7 21l6-7 5 5 8-9" stroke="var(--icon)" stroke-width="2" fill="none"/><circle cx="30" cy="27" r="6" fill="#fff" stroke="var(--icon)" stroke-width="3"/><path d="M34 31l6 6" stroke="var(--icon)" stroke-width="4"/></svg></div>
      <div class="service-name">Financial<br>Analysis</div></div>
    <div class="service abs" style="left:645px;top:64px">
      <div class="service-icon"><svg width="42" height="38" viewBox="0 0 42 38"><rect x="14" y="3" width="14" height="7" rx="2" fill="none" stroke="var(--icon)" stroke-width="3"/><rect x="3" y="9" width="36" height="25" rx="3" fill="var(--icon)"/><rect x="3" y="19" width="36" height="2" fill="#fff"/><rect x="18" y="16" width="6" height="8" fill="#fff"/></svg></div>
      <div class="service-name">Cash Management<br>Solutions</div></div>
  </section>

  <h3 class="col-title abs" style="left:103px;top:759px">
    <svg width="18" height="13"><path d="M1 4h4l7-3v11L5 9H1z" fill="#444"/></svg><b>Latest</b> News</h3>
  <div class="news-item abs" style="left:105px;top:795px"><strong>09/10/2014</strong>Lorem ipsum dolor sit amet, cctetuer adipiscingin elit, sed diam nummy nibh eui smod tinciduntiot vulputate velit esse molestie</div>
  <div class="abs" style="left:105px;top:853px;width:205px;border-top:1px dashed #ccc"></div>
  <div class="news-item abs" style="left:105px;top:859px"><strong>10/10/2014</strong>Lorem ipsum dolor sit amet, cctetuer adipiscingin elit, sed diam nummy nibh eui smod tinciduntiot vulputate velit esse molestie</div>
  <span class="read-more abs" style="left:258px;top:922px">Read more »</span>

  <h3 class="col-title abs" style="left:337px;top:759px">
    <svg width="18" height="15"><rect x="0" y="0" width="12" height="9" rx="2" fill="#444"/><rect x="5" y="4" width="12" height="8" rx="2" fill="#666"/></svg><b>Client</b> Testimonial</h3>
  <div class="quote abs">Duis autem vel eum iriureol hder in vultat velit esse moles conqat vela ilu dolor feugiat.Duis autem vel eum ure hendrern vultat velit esse autm vel eum iriure dol</div>
  <div class="avatar abs" role="img" aria-label="Client portrait photo"></div>
  <span class="abs" style="left:412px;top:904px;font-size:9px;color:#222">Mr. Aldo Venner</span>
  <span class="read-more abs" style="left:493px;top:923px">Read more »</span>

  <h3 class="col-title abs" style="left:571px;top:759px">
    <svg width="16" height="14"><rect x="1" y="2" width="10" height="11" fill="none" stroke="#444" stroke-width="1.5"/><path d="M8 9l6-7 1.5 1.5-6 7H8z" fill="#444"/></svg><b>Quick</b> Contact</h3>
  <div class="field abs" style="left:571px;top:797px;height:21px">Name</div>
  <div class="field abs" style="left:571px;top:823px;height:21px">Email</div>
  <div class="field abs" style="left:571px;top:849px;height:53px">Message</div>
  <div class="submit abs">Submit</div>

  <section class="clients abs">
    <h2 class="section-title abs" style="left:0;top:13px;width:882px">Our <b>Clients</b></h2>
    <div class="round-arrow abs" style="left:82px;top:64px;width:22px;height:22px"><svg width="6" height="8"><path d="M5 1L1 4l4 3" stroke="#fff" stroke-width="1.4" fill="none"/></svg></div>
    <div class="round-arrow abs" style="left:779px;top:64px;width:22px;height:22px"><svg width="6" height="8"><path d="M1 1l4 3-4 3" stroke="#fff" stroke-width="1.4" fill="none"/></svg></div>
    <div class="client abs" style="left:117px;top:53px;width:104px">Norvell Tech</div>
    <div class="client abs" style="left:231px;top:53px;width:116px">Arlo Works</div>
    <div class="client abs" style="left:356px;top:53px;width:139px">Greenhollow</div>
    <div class="client abs" style="left:517px;top:53px;width:100px"><i></i>Tessivo</div>
    <div class="client abs" style="left:637px;top:53px;width:130px">Ledgerleaf</div>
  </section>

  <footer class="site-footer abs">
    <div class="footer-box abs" style="left:103px;width:181px">Subscribe to Newsletter
      <div style="display:flex;gap:6px;margin-top:7px">
        <div style="width:132px;height:19px;background:#666;border:1px solid #777;font-size:8.5px;font-style:italic;font-weight:400;color:#ddd;padding:3px 6px">Email here</div>
        <div style="width:22px;height:19px;background:#777;display:flex;align-items:center;justify-content:center"><svg width="7" height="9"><path d="M1 1l4 3.5L1 8" stroke="#fff" stroke-width="1.8" fill="none"/></svg></div>
      </div>
    </div>
    <div class="footer-box abs" style="left:304px;width:118px">Contact Us
      <p><svg width="9" height="9"><path d="M1 1l2 .5 1 2-1 1c.5 1 1.5 2 2.5 2.5l1-1 2 1L8 9C4 8.5 1 5 1 1z" fill="#ccc"/></svg>555 010 2040</p>
      <p><svg width="10" height="8"><rect width="10" height="8" fill="#ccc"/><path d="M0 0l5 4 5-4" stroke="#555" fill="none"/></svg>info@brivane.com</p>
    </div>
    <div class="footer-box abs" style="left:443px;width:87px">Follow Us
      <div class="social-row"><span class="social" style="background:#3b5a9a"></span><span class="social" style="background:#28a9e0"></span><span class="social" style="background:#1a75b4"></span></div>
    </div>
    <div class="brand abs"><span class="brand-dot"></span>BRIVANE MANAGEMENT</div>
    <div class="footer-links abs">Home <span>|</span> About Us <span>|</span> Services <span>|</span> Contact Us <span>|</span> Terms Conditions</div>
    <div class="copyright abs">© 2014 &nbsp;Brivane. All Rights Reserved</div>
  </footer>
</body>
</html>
```